Stylish new business card needed!

Hello everyone! I am in need of a new business card design for an alarm company here in Hurricane WV. I have all fonts, color codes and logos provided for you use! We are a young company and like the style of a clean sleek looking business card. Would like it double sided, one side holding the logo and the other with your design!
Target Market(s)
The people that are looking for the newest tech for home automation and security
Industry/Entity Type
Alarm services; Home automation
Contact Information for Business Card
Name of person; position (Sales; Installer); Phone Number (555.418.7260); Employee cell Number; Website (www.GuardedByVelk.example); Employee Email; Double sided
Look and feel
Each slider illustrates characteristics of the customer's brand and the style your logo design should communicate.

```html
<!DOCTYPE html>
<html lang="en">
<head>
<meta charset="utf-8">
<title>Velk business card</title>
<link rel="stylesheet" href="https://fonts.googleapis.com/css2?family=Open+Sans:wght@300;400;600;700;800&display=swap">
<style>
  :root {
    --page: #2b2d31;
    --card: #1f1e22;
    --orange: #ec8a4c;
    --grey: #9a9a9c;
    --white: #f4f4f4;
    --pattern-a: #1a1a1d;
    --pattern-b: #2a2a2e;
  }
  * { margin: 0; padding: 0; box-sizing: border-box; }
  html, body { width: 1200px; height: 780px; overflow: hidden; }
  body {
    background: var(--page);
    font-family: "Open Sans", Arial, sans-serif;
    display: flex;
    align-items: center;
    justify-content: center;
    gap: 40px;
  }
  .card {
    position: relative;
    width: 540px;
    height: 309px;
    background: var(--card);
    overflow: hidden;
    box-shadow: 0 10px 30px rgba(0,0,0,.45);
  }
  .card__swoosh { position: absolute; inset: 0; width: 100%; height: 100%; }
  .brand {
    position: absolute;
    top: 34px;
    right: 62px;
    font-size: 76px;
    font-weight: 300;
    letter-spacing: 2px;
    color: var(--grey);
    line-height: 1;
  }
  .holder { position: absolute; top: 36px; left: 34px; }
  .holder__name { font-size: 24px; font-weight: 800; line-height: 1.1; }
  .holder__first { color: var(--orange); }
  .holder__last { color: var(--grey); }
  .holder__role { margin-top: 4px; font-size: 15px; font-weight: 600; color: var(--white); }
  .divider {
    position: absolute;
    left: 214px;
    top: 150px;
    width: 2px;
    height: 92px;
    background: var(--white);
  }
  .contacts {
    position: absolute;
    left: 232px;
    top: 150px;
    list-style: none;
  }
  .contacts__item {
    display: flex;
    align-items: center;
    gap: 9px;
    font-size: 14px;
    color: var(--white);
    line-height: 23px;
  }
  .contacts__icon { width: 13px; height: 13px; flex: none; }
  .back__pattern { position: absolute; inset: 0; background: linear-gradient(125deg, var(--pattern-a) 0%, var(--pattern-b) 55%, var(--pattern-a) 100%); }
  .back__brand {
    position: absolute;
    right: 44px;
    bottom: 34px;
    font-size: 30px;
    font-weight: 300;
    letter-spacing: 1px;
    color: var(--orange);
  }
</style>
</head>
<body>
  <section class="card card--front">
    <svg class="card__swoosh" viewBox="0 0 540 309" preserveAspectRatio="none" aria-hidden="true">
      <path d="M0 232 C40 222 60 212 78 206 C150 300 360 312 540 300 L540 309 L0 309 Z" fill="var(--orange)"/>
      <path d="M86 200 C150 290 360 306 530 296" fill="none" stroke="var(--grey)" stroke-width="5" stroke-linecap="round"/>
    </svg>

    <div class="brand">Velk</div>

    <div class="holder">
      <p class="holder__name"><span class="holder__first">Marta</span> <span class="holder__last">Kovalenko</span></p>
      <p class="holder__role">Sales; Installer</p>
    </div>

    <div class="divider"></div>

    <ul class="contacts">
      <li class="contacts__item">
        <svg class="contacts__icon" viewBox="0 0 16 16"><path d="M3 1h3l1.5 4-2 1.3a9 9 0 0 0 4.2 4.2L11 8.5l4 1.5v3c0 1-1 2-2 2C6.4 15 1 9.6 1 3c0-1 1-2 2-2z" fill="var(--orange)"/></svg>
        555.418.7260
      </li>
      <li class="contacts__item">
        <svg class="contacts__icon" viewBox="0 0 16 16"><rect x="4" y="1" width="8" height="14" rx="1.5" fill="none" stroke="var(--orange)" stroke-width="1.6"/><circle cx="8" cy="12.5" r=".9" fill="var(--orange)"/></svg>
        555.302.9184
      </li>
      <li class="contacts__item">
        <svg class="contacts__icon" viewBox="0 0 16 16"><circle cx="8" cy="8" r="6.5" fill="none" stroke="var(--orange)" stroke-width="1.6"/><path d="M1.5 8h13M8 1.5c-3 3.5-3 9.5 0 13M8 1.5c3 3.5 3 9.5 0 13" fill="none" stroke="var(--orange)" stroke-width="1.2"/></svg>
        www.GuardedByVelk.example
      </li>
      <li class="contacts__item">
        <svg class="contacts__icon" viewBox="0 0 16 16"><rect x="1" y="3" width="14" height="10" rx="1" fill="var(--orange)"/><path d="M1.5 3.5 8 9l6.5-5.5" fill="none" stroke="var(--card)" stroke-width="1.3"/></svg>
        info@GuardedByVelk.example
      </li>
    </ul>
  </section>

  <section class="card card--back">
    <div class="back__pattern" role="img" aria-label="Dark repeating brand wordmark pattern in glossy spot finish"></div>
    <div class="back__brand">Velk</div>
  </section>
</body>
</html>
```